Halvery Construction Group Website

Need a dynamic corporate website that can be built on with time. We want to get our information out to the world and have a place where customers can submit requests for proposals.

Target Market(s)

Custom home owners and buyers. Architects and Real Estate Agents.

Industry/Entity Type

Construction

Number of Pages Required

3 page

Font styles to use
Serif
Sans Serif

Requirements
Must have
• Company logo, about, company contact information, biography, contact, projects,
• Sleek, modern, clean, attractive design.
• Online form customers can use for filling out a request for project proposal.
• Linkedin hyperlink.
• Uses www.halveryconstructiongroup.example

```html
<!DOCTYPE html>
<html lang="en">
<head>
<meta charset="utf-8">
<title>Halvery Construction Group</title>
<link href="https://fonts.googleapis.com/css2?family=Montserrat:wght@300;400;500&family=Open+Sans:wght@300;400&display=swap" rel="stylesheet">
<style>
:root{
  --white:#ffffff;
  --hero-top:#5f7f8c;
  --hero-bottom:#9a8a6e;
  --ink:#333333;
  --muted:#666666;
  --brand:#1f4fa8;
  --rule:#d8d8d8;
  --icon-bg:#e2e2e2;
}
*{margin:0;padding:0;box-sizing:border-box}
html,body{width:1200px;height:923px;overflow:hidden;background:var(--white)}
body{position:relative;font-family:"Open Sans",sans-serif;color:var(--ink)}
.hero{position:absolute;left:0;top:0;width:1200px;height:572px;overflow:hidden}
.hero-photo{position:absolute;inset:0;background:linear-gradient(180deg,var(--hero-top) 0%,var(--hero-bottom) 100%)}
.brand{position:absolute;left:127px;top:24px;display:flex;align-items:center;gap:14px;color:var(--white);font-family:"Montserrat",sans-serif;font-weight:500}
.brand-square{width:72px;height:68px;background:var(--white)}
.brand-name{font-size:38px;line-height:1;letter-spacing:.5px}
.brand-name small{display:block;font-size:13.5px;font-weight:400;letter-spacing:0;margin-top:4px}
.main-nav{position:absolute;top:51px;left:591px;display:flex;gap:40px;font-family:"Montserrat",sans-serif;font-size:15.5px;font-weight:500;color:var(--white)}
.headline{position:absolute;left:132px;top:262px;color:var(--white);font-family:"Montserrat",sans-serif;font-weight:300;line-height:1}
.headline .line1{font-size:43px;display:block}
.headline .line2{font-size:57px;display:block;margin-top:9px;letter-spacing:.5px}
.dots{position:absolute;left:551px;top:525px;display:flex;gap:4px}
.dots span{width:18px;height:18px;border-radius:50%;background:var(--white)}
.dots span.active{background:transparent;border:2px solid var(--white)}
.footer-col{position:absolute;top:626px}
.footer-col h3{font-family:"Montserrat",sans-serif;font-weight:400;font-size:21px;color:var(--ink);margin-bottom:14px}
.footer-col a{display:block;font-weight:300;font-size:15px;color:var(--ink);text-decoration:none;margin-bottom:11px}
.col-projects{left:124px}
.col-resources{left:335px;top:629px}
.col-follow{left:557px}
.social{display:flex;gap:9px;margin-top:4px}
.social span{width:37px;height:37px;border-radius:50%;background:var(--icon-bg)}
.footer-brand{position:absolute;left:850px;top:629px;width:224px;display:flex;flex-direction:column;align-items:center;color:var(--brand);font-family:"Montserrat",sans-serif;font-weight:500;text-align:center}
.footer-brand .mark{width:72px;height:65px;background:var(--brand);margin-bottom:14px}
.footer-brand .name{font-size:40px;line-height:1}
.footer-brand .sub{font-size:13.5px;line-height:1;margin-top:4px}
.rule{position:absolute;left:122px;top:842px;width:950px;height:1px;background:var(--rule)}
.copyright{position:absolute;left:119px;top:872px;font-size:13px;color:var(--muted)}
.footer-nav{position:absolute;top:867px;left:699px;display:flex;gap:34px;font-size:15px;color:var(--ink)}
</style>
</head>
<body>
<section class="hero">
  <div class="hero-photo" role="img" aria-label="Photo of modern apartment buildings under a sunny sky"></div>
  <div class="brand"><div class="brand-square"></div><div class="brand-name">HALVERY<small>CONSTRUCTION GROUP, INC.</small></div></div>
  <nav class="main-nav"><span>HOME</span><span>ABOUT</span><span>BIO</span><span>PROJECTS</span><span>CONTACT US</span></nav>
  <h1 class="headline"><span class="line1">WORLD CLASS</span><span class="line2">CONSTRUCTION</span></h1>
  <div class="dots"><span class="active"></span><span></span><span></span><span></span></div>
</section>

<div class="footer-col col-projects"><h3>Projects</h3><a>Commercial</a><a>Residential</a><a>Community</a><a>Location Map</a></div>
<div class="footer-col col-resources"><h3>Resources</h3><a>Our Team</a><a>Support</a><a>Testimonials</a></div>
<div class="footer-col col-follow"><h3>Follow Us</h3>
  <div class="social"><span aria-label="Social link"></span><span aria-label="Social link"></span><span aria-label="Video channel"></span><span aria-label="Professional network"></span><span aria-label="Social link"></span></div>
</div>
<div class="footer-brand"><div class="mark"></div><div class="name">HALVERY</div><div class="sub">CONSTRUCTION GROUP, INC.</div></div>

<div class="rule"></div>
<p class="copyright">© 2016 Company Name&nbsp; All right reserved&nbsp; Term of Use</p>
<nav class="footer-nav"><span>Home</span><span>About</span><span>Bio</span><span>Projects</span><span>Contact us</span></nav>
</body>
</html>
```